Business card design needed

I would like a one sided black business card with the information provided above. Refer to my website www.brightvolleyracquets.com.au for an example of colors I have used for my site, would like to keep this consistent for my business cards also, I will upload my logo below.

I am a new small business that provides tennis customers with racquet re stringing, tennis strings and accessories.

Industry/Entity Type

Small Business

Contact Information for Business Card

Bright Volley Tennis

Owen Whitby
Managing Director

brightvolleyracquets@mailbox.example
www.brightvolleyracquets.com.au
0491 726 305

Racquet Restringing/Tennis Strings/Accessories

Requirements
Must have
• Must have my logo and card must be black

```html
<!DOCTYPE html>
<html lang="en">
<head>
<meta charset="utf-8">
<title>Bright Volley Tennis – Business Card</title>
<link rel="stylesheet" href="https://fonts.googleapis.com/css2?family=Open+Sans:wght@400;600;700&display=swap">
<style>
  :root {
    --backdrop: #e9e7e4;
    --card: #000000;
    --lime: #b8d433;
    --white: #ffffff;
    --font: "Open Sans", Arial, sans-serif;
  }
  * { box-sizing: border-box; margin: 0; padding: 0; }
  html, body {
    width: 1200px; height: 475px; overflow: hidden;
    background: var(--backdrop);
    font-family: var(--font);
  }
  .stage { position: relative; width: 1200px; height: 475px; }
  .card {
    position: absolute; top: 81px;
    width: 547px; height: 313px;
    background: var(--card);
    overflow: hidden;
  }
  .card--front { left: 40px; }
  .card--back { left: 602px; }

  .brand {
    position: absolute;
    display: flex; align-items: center; gap: 12px;
    color: var(--lime);
    font-family: var(--font);
    font-weight: 700;
    font-size: 34px;
    letter-spacing: 0.5px;
    white-space: nowrap;
  }
  .brand__dot {
    width: 30px; height: 30px; border-radius: 50%;
    background: var(--lime); flex: none;
  }
  .card--front .brand { left: 38px; top: 70px; }
  .card--back .brand { left: 50%; top: 126px; transform: translateX(-50%); }

  .edge-tab {
    position: absolute; width: 7px; background: var(--lime);
  }
  .edge-tab--left { left: 0; top: 184px; height: 105px; border-radius: 0 5px 5px 0; }
  .edge-tab--right { right: 0; top: 199px; height: 58px; border-radius: 5px 0 0 5px; }

  .contacts {
    position: absolute; left: 28px; top: 203px;
    list-style: none;
  }
  .contacts li {
    display: flex; align-items: center; gap: 11px;
    height: 20px;
    color: var(--white); font-size: 13px;
  }
  .contacts svg { width: 11px; height: 11px; flex: none; }

  .person {
    position: absolute; right: 26px; top: 205px;
    text-align: right; color: var(--lime);
  }
  .person__name { font-size: 16px; font-weight: 400; letter-spacing: 0.3px; }
  .person__role { font-size: 13px; margin-top: 1px; }

  .card__url {
    position: absolute; left: 0; right: 0; top: 260px;
    text-align: center;
    color: var(--white); font-size: 13px; letter-spacing: 2.2px;
  }
</style>
</head>
<body>
<main class="stage">
  <section class="card card--front" aria-label="Card front">
    <div class="brand"><span class="brand__dot"></span>Bright Volley Tennis</div>
    <span class="edge-tab edge-tab--left"></span>
    <span class="edge-tab edge-tab--right"></span>
    <ul class="contacts">
      <li>
        <svg viewBox="0 0 12 12" aria-hidden="true"><path fill="var(--lime)" d="M2.5 1l2 2.2-1 1.3a6.5 6.5 0 0 0 4 4l1.3-1 2.2 2-1.2 1.5C5.5 11 1 6.5.9 2.2z"/></svg>
        0491 726 305
      </li>
      <li>
        <svg viewBox="0 0 12 12" aria-hidden="true"><rect x="1" y="2.5" width="10" height="7" fill="var(--lime)"/><path d="M1 2.5l5 4 5-4" fill="none" stroke="#000" stroke-width="1"/></svg>
        brightvolleyracquets@mailbox.example
      </li>
      <li>
        <svg viewBox="0 0 12 12" aria-hidden="true"><circle cx="6" cy="6" r="5" fill="var(--lime)"/><path d="M1 6h10M6 1c-2.5 3-2.5 7 0 10M6 1c2.5 3 2.5 7 0 10" fill="none" stroke="#000" stroke-width=".8"/></svg>
        www.brightvolleyracquets.com.au
      </li>
    </ul>
    <div class="person">
      <p class="person__name">OWEN WHITBY</p>
      <p class="person__role">Managing Director</p>
    </div>
  </section>

  <section class="card card--back" aria-label="Card back">
    <div class="brand"><span class="brand__dot"></span>Bright Volley Tennis</div>
    <p class="card__url">www.brightvolleyracquets.com.au</p>
  </section>
</main>
</body>
</html>
```